New Mechanical Maintenance business needs website

New Mechanical Maintenance business in Perth Western Australia needs a nice and easy to navigate website. Showing what we do and how we can be the right fit for other small to medium size business by offering personalized service from our highly skilled team. We deal with both fixed plant repairs like food and chemical processing facilities to heavy equipment like drill rigs, Large boats and earthmoving equipment.

Target Market(s)

Small to medium business to offer personalized services/packages

Industry/Entity Type

e deal with both fixed plant repairs like food and chemical processing facilities to heavy equipment like drill rigs, Large boats and earthmoving equipment.

Coding

Coded - Design and coding required

Number of Pages Required

4 page

Font styles to use
Serif

Colors
0054AA
0677BA
7BADD7
CADEEF
E8F1F8

Requirements
Must have
• A website that is easy to navigate but covers off on the range of services/maintenance we can provide

```html
<!DOCTYPE html>
<html lang="en">
<head>
<meta charset="utf-8">
<title>Ridgeline Maintenance</title>
<link rel="stylesheet" href="https://fonts.googleapis.com/css2?family=Oswald:wght@400;500&family=Poppins:wght@400;600&display=swap">
<style>
:root{
  --blue:#0054aa;
  --blue-mid:#0677ba;
  --blue-soft:#7badd7;
  --blue-pale:#cadeef;
  --blue-wash:#e8f1f8;
  --slate:#4a5f80;
  --ink:#222;
  --text:#555;
  --footer:#5a5d63;
  --white:#fff;
}
*{margin:0;padding:0;box-sizing:border-box}
html,body{width:1200px;height:5381px;overflow:hidden}
body{position:relative;background:var(--white);font-family:'Poppins',sans-serif;color:var(--text)}
.abs{position:absolute}
.display{font-family:'Oswald',sans-serif;text-transform:uppercase}
.btn{position:absolute;display:flex;align-items:center;justify-content:center;background:var(--slate);color:var(--white);font-family:'Oswald',sans-serif;font-size:21px;text-transform:uppercase;letter-spacing:.5px}
.photo{position:absolute}
.section-title{position:absolute;left:0;width:1200px;text-align:center;font-family:'Oswald',sans-serif;font-size:44px;color:#333;text-transform:uppercase}
.body-copy{font-size:14.5px;line-height:28px;color:var(--text)}

/* header */
.brand{left:75px;top:32px;display:flex;align-items:center;gap:12px;font-family:'Oswald',sans-serif;font-size:24px;color:#444;text-transform:uppercase}
.brand-dot{width:44px;height:44px;border-radius:50%;border:4px solid #555}
.phone{right:75px;top:26px;font-family:'Oswald',sans-serif;font-size:21px;color:var(--blue);text-transform:uppercase;display:flex;align-items:center;gap:8px}
.nav{right:75px;top:82px;display:flex;gap:42px;font-family:'Oswald',sans-serif;font-size:17px;text-transform:uppercase;color:#333}
.nav .active{color:var(--blue-mid)}

/* hero */
.hero{left:0;top:125px;width:1200px;height:736px;background:linear-gradient(180deg,#4a4f6c 0%,#7b6b78 35%,#5d6478 60%,#3c4458 100%)}
.hero-kicker{top:356px;width:1200px;text-align:center;font-family:'Oswald',sans-serif;font-size:42px;line-height:54px;color:var(--white)}
.hero-title{top:398px;width:1200px;text-align:center;font-family:'Oswald',sans-serif;font-size:82px;color:var(--white);line-height:96px}
.hero-sub{top:498px;width:1200px;text-align:center;font-size:22px;font-weight:600;color:var(--white)}
.dots{top:806px;left:525px;display:flex;gap:8px}
.dots span{width:33px;height:6px;background:#111}
.dots span:first-child{background:var(--blue-soft)}

/* about */
.about-title{left:118px;top:958px;width:480px;white-space:nowrap;font-size:36px;line-height:48px;color:#333}

.band{position:absolute;left:0;width:1200px;background:var(--blue-wash)}
.card-title{font-family:'Oswald',sans-serif;font-size:20px;color:var(--blue);text-transform:uppercase;line-height:28px}
.card-text{font-size:14px;line-height:26px;color:var(--text);margin-top:6px}
.news-title{font-family:'Oswald',sans-serif;font-size:25px;color:#222;text-transform:uppercase;line-height:32px}

/* footer */
.footer{left:0;top:4748px;width:1200px;height:633px;background:var(--footer);color:var(--white)}
.foot-head{font-family:'Oswald',sans-serif;font-size:28px;text-transform:uppercase;color:var(--white)}
.foot-links{list-style:none;font-size:16px;line-height:40px}
.contact-row{display:flex;gap:16px;align-items:flex-start;font-size:16px;line-height:26px}
.icon-ring{flex:none;width:44px;height:44px;border:2px solid var(--white);border-radius:50%;display:flex;align-items:center;justify-content:center}
.field{position:absolute;background:var(--white);color:#333;font-size:13px;padding:16px 14px}
.social{display:flex;gap:22px}
.social span{width:20px;height:20px;border-radius:50%;background:var(--white)}
</style>
</head>
<body>

<!-- header -->
<div class="abs brand"><span class="brand-dot"></span>Ridgeline Maintenance</div>
<div class="abs phone">
  <svg width="18" height="18" viewBox="0 0 24 24"><path d="M6.6 10.8c1.4 2.8 3.8 5.1 6.6 6.6l2.2-2.2c.3-.3.7-.4 1-.2 1.1.4 2.3.6 3.6.6.6 0 1 .4 1 1V20c0 .6-.4 1-1 1C10.6 21 3 13.4 3 4c0-.6.4-1 1-1h3.5c.6 0 1 .4 1 1 0 1.3.2 2.5.6 3.6.1.3 0 .7-.2 1L6.6 10.8z" fill="#0054aa"/></svg>
  Call us today on: +61 8 5550 1234
</div>
<nav class="abs nav">
  <span class="active">Home</span><span>About Us</span><span>Services</span><span>Portfolio</span><span>News</span><span>Careers</span><span>Contact</span>
</nav>

<!-- hero -->
<div class="abs hero" role="img" aria-label="Industrial refinery with storage tanks at dusk"></div>
<div class="abs hero-kicker display">Welcome to</div>
<div class="abs hero-title display">Ridgeline Maintenance</div>
<div class="abs hero-sub">Sed ut perspiciatis unde omnis iste natus error sit voluptate.</div>
<div class="btn" style="left:496px;top:562px;width:208px;height:58px;background:var(--blue)">Read More</div>
<div class="abs dots"><span></span><span></span><span></span><span></span></div>

<!-- about -->
<div class="abs display about-title">About Ridgeline Maintenance</div>
<p class="abs" style="left:75px;top:1056px;width:510px;font-size:16px;line-height:30px;font-weight:600;color:var(--blue)">Director of the company has over 20-year experience in the fixed and mobile plant industries ranging from Perth local and overseas.</p>
<p class="abs body-copy" style="left:75px;top:1157px;width:520px">Sed ut perspiciatis unde omnis iste natus error sit voluptatem accusantium doloremque laudantium, totam rem aperiam, eaque ipsa quae ab illo inventore veritatis et quasi architecto beatae vitae dicta sunt explicabo.</p>
<div class="btn" style="left:75px;top:1290px;width:180px;height:61px">Read More</div>
<div class="photo" style="left:615px;top:930px;width:512px;height:420px;background:linear-gradient(135deg,#2c3a4e,#5a6a7c 55%,#2a3240)" role="img" aria-label="Two mechanics inspecting an engine"></div>

<!-- services -->
<div class="band" style="top:1438px;height:625px"></div>
<div class="section-title" style="top:1514px">Our Services</div>
<svg class="abs" style="left:42px;top:1783px" width="16" height="26" viewBox="0 0 16 26"><path d="M13 2 3 13l10 11" fill="none" stroke="#0677ba" stroke-width="2.5"/></svg>
<svg class="abs" style="left:1138px;top:1783px" width="16" height="26" viewBox="0 0 16 26"><path d="M3 2l10 11L3 24" fill="none" stroke="#0677ba" stroke-width="2.5"/></svg>

<div class="photo" style="left:75px;top:1639px;width:328px;height:213px;background:linear-gradient(135deg,#3a2414,#b0642a 50%,#2b1c12)" role="img" aria-label="Worker in a refinery pipe corridor"></div>
<div class="photo" style="left:437px;top:1639px;width:328px;height:213px;background:linear-gradient(135deg,#4b5b6b,#2f3944 60%,#7a8894)" role="img" aria-label="Technician working on an offshore platform"></div>
<div class="photo" style="left:798px;top:1639px;width:329px;height:213px;background:linear-gradient(135deg,#c98a3c,#6b5a44 55%,#3b342c)" role="img" aria-label="Mine workers at an open cut site"></div>

<div class="abs" style="left:75px;top:1872px;width:328px"><div class="card-title">Precious Metals<br>Refining</div><p class="card-text">Sed ut perspiciatis unde omnis iste natus error sit voluptatem accusantium..</p></div>
<div class="abs" style="left:437px;top:1872px;width:328px"><div class="card-title">Offshore Drilling<br>&amp; Production Platform</div><p class="card-text">Sed ut perspiciatis unde omnis iste natus error sit voluptatem accusantium..</p></div>
<div class="abs" style="left:798px;top:1872px;width:329px"><div class="card-title">Open Cut &amp;<br>Underground Mining</div><p class="card-text">Sed ut perspiciatis unde omnis iste natus error sit voluptatem accusantium..</p></div>
<div class="btn" style="left:496px;top:2032px;width:208px;height:60px">View All Services</div>

<!-- personalised -->
<div class="section-title" style="top:2198px">Personalised Service</div>
<div class="abs display" style="left:73px;top:2375px;font-size:32px;color:var(--blue)">Small and Medium Size Business</div>
<p class="abs body-copy" style="left:75px;top:2428px;width:555px">Sed ut perspiciatis unde omnis iste natus error sit voluptatem accusantium doloremque laudantium, totam rem aperiam, eaque ipsa quae ab illo inventore veritatis et quasi architecto beatae vitae dicta sunt explicabo.</p>
<p class="abs body-copy" style="left:75px;top:2545px;width:555px">Sed ut perspiciatis unde omnis iste natus error sit voluptatem accusantium doloremque laudantium, totam rem aperiam, eaque ipsa quae ab illo inventore veritatis et quasi.</p>
<div class="btn" style="left:75px;top:2644px;width:180px;height:61px">Read More</div>
<div class="photo" style="left:615px;top:2333px;width:512px;height:422px;background:linear-gradient(135deg,#5a6470,#8a9aa6 45%,#c7c2a0 70%,#3a4450)" role="img" aria-label="Engineer in hard hat operating a machine"></div>
<div class="abs" style="left:615px;top:2352px;width:58px;height:350px;background:var(--white)"></div>

<!-- our work -->
<div class="band" style="top:2838px;height:1083px"></div>
<div class="section-title" style="top:2914px">Our Work</div>
<div class="photo" style="left:77px;top:3041px;width:510px;height:374px;background:linear-gradient(135deg,#3a3a3e,#6a5a48 50%,#2a3040)" role="img" aria-label="Two workers in hard hats reviewing plans"></div>
<div class="photo" style="left:615px;top:3041px;width:512px;height:374px;background:linear-gradient(180deg,#c98a5a,#5a6c8a 45%,#2a3a52)" role="img" aria-label="Processing plant at sunset"></div>
<div class="photo" style="left:77px;top:3440px;width:510px;height:374px;background:linear-gradient(135deg,#2e2c2a,#8a5a30 55%,#3a3634)" role="img" aria-label="Mechanic repairing an engine"></div>
<div class="photo" style="left:615px;top:3440px;width:512px;height:374px;background:linear-gradient(135deg,#4a6a84,#7a4a3a 50%,#3a6a80)" role="img" aria-label="Worker on a ship hull beside the propeller"></div>
<div class="btn" style="left:496px;top:3892px;width:208px;height:60px">View All Work</div>

<!-- news -->
<div class="section-title" style="top:4042px">Latest News</div>
<div class="photo" style="left:75px;top:4163px;width:328px;height:230px;background:linear-gradient(135deg,#4a5058,#8a8c90 50%,#2e3238)" role="img" aria-label="Engineers inspecting machinery"></div>
<div class="photo" style="left:437px;top:4163px;width:328px;height:230px;background:linear-gradient(135deg,#2a2e36,#c0843a 55%,#3a3a40)" role="img" aria-label="Welder with sparks"></div>
<div class="photo" style="left:798px;top:4163px;width:329px;height:230px;background:linear-gradient(135deg,#6a5a70,#3a3640 55%,#8a8088)" role="img" aria-label="Mechanic using a power tool"></div>
<div class="abs" style="left:75px;top:4418px;width:330px"><div class="news-title">Nemo enim ipsam voluptatem quia voluptas</div><p class="card-text">Sed ut perspiciatis unde omnis iste natus error sitvo dolores eos qui ratione voluptatem sequi.</p></div>
<div class="abs" style="left:437px;top:4418px;width:330px"><div class="news-title">Nemo enim ipsam voluptatem quia voluptas</div><p class="card-text">Sed ut perspiciatis unde omnis iste natus error sitvo dolores eos qui ratione voluptatem sequi.</p></div>
<div class="abs" style="left:798px;top:4418px;width:330px"><div class="news-title">Nemo enim ipsam voluptatem quia voluptas</div><p class="card-text">Sed ut perspiciatis unde omnis iste natus error sitvo dolores eos qui ratione voluptatem sequi.</p></div>
<div class="btn" style="left:496px;top:4610px;width:208px;height:61px">View All News</div>

<!-- footer -->
<footer class="abs footer">
  <div class="abs foot-head" style="left:75px;top:82px">Site Map</div>
  <ul class="abs foot-links" style="left:75px;top:142px">
    <li>Home</li><li>About Us</li><li>Services</li><li>Portfolio</li><li>News</li><li>Careers</li><li>Contact</li>
  </ul>

  <div class="abs foot-head" style="left:343px;top:82px">Contact Us</div>
  <div class="abs contact-row" style="left:343px;top:142px;width:320px">
    <span class="icon-ring"><svg width="18" height="18" viewBox="0 0 24 24"><path d="M12 2a7 7 0 0 0-7 7c0 5 7 13 7 13s7-8 7-13a7 7 0 0 0-7-7zm0 9.5a2.5 2.5 0 1 1 0-5 2.5 2.5 0 0 1 0 5z" fill="#fff"/></svg></span>
    <div>ADDRESS:<br>48 Harbour Lane, Suite 3<br>Fremantle WA</div>
  </div>
  <div class="abs contact-row" style="left:343px;top:246px">
    <span class="icon-ring"><svg width="18" height="18" viewBox="0 0 24 24"><path d="M6.6 10.8c1.4 2.8 3.8 5.1 6.6 6.6l2.2-2.2c.3-.3.7-.4 1-.2 1.1.4 2.3.6 3.6.6.6 0 1 .4 1 1V20c0 .6-.4 1-1 1C10.6 21 3 13.4 3 4c0-.6.4-1 1-1h3.5c.6 0 1 .4 1 1 0 1.3.2 2.5.6 3.6.1.3 0 .7-.2 1L6.6 10.8z" fill="#fff"/></svg></span>
    <div>PHONE:<br>+61 8 5550 1234</div>
  </div>
  <div class="abs contact-row" style="left:343px;top:324px">
    <span class="icon-ring"><svg width="18" height="18" viewBox="0 0 24 24"><path d="M3 5h18v14H3z" fill="#fff"/><path d="M3 5l9 7 9-7" fill="none" stroke="#5a5d63" stroke-width="2"/></svg></span>
    <div>EMAIL:<br>info@ridgelinemaint.com</div>
  </div>
  <div class="abs social" style="left:343px;top:425px"><span></span><span></span><span></span><span></span><span></span></div>

  <div class="abs foot-head" style="left:703px;top:82px">Contact Form</div>
  <div class="field" style="left:703px;top:146px;width:206px;height:51px">Name</div>
  <div class="field" style="left:921px;top:146px;width:206px;height:51px">Email Address</div>
  <div class="field" style="left:703px;top:211px;width:206px;height:51px">Phone No</div>
  <div class="field" style="left:921px;top:211px;width:206px;height:51px">Subject</div>
  <div class="field" style="left:703px;top:276px;width:424px;height:120px">Message</div>
  <div class="btn" style="left:703px;top:410px;width:206px;height:52px;background:var(--blue-soft)">Submit</div>

  <div class="abs" style="left:0;top:588px;width:1200px;text-align:center;font-size:13px">Copyright © 2024 Ridgeline Maintenance - All Rights Reserved</div>
</footer>

</body>
</html>
```